BOLD & MINIMALIST DESIGN NEEDED

We want a very bold but minimalistic business card design that is impactful and utilizes both sides of the business card. Our current logo is included for your use.

We want bold fonts and good use of negative space. We don't want the logo to overpower the design.

Target Market(s)

Professionals who are building new commercial buildings.

Industry/Entity Type

Construction

Contact Information for Business Card

Name, Title, email, office phone, cell phone, website

Font styles to use
Serif
Sans Serif

Requirements
Must have
• Bold design!

```html
<!DOCTYPE html>
<html lang="en">
<head>
<meta charset="utf-8">
<title>Tallbrook Design + Build — Business Card</title>
<link rel="stylesheet" href="https://fonts.googleapis.com/css2?family=Montserrat:wght@400;500;600;700;800&display=swap">
<style>
  :root {
    --stage: #d9d9d9;
    --card: #1e1e1e;
    --ink-white: #ffffff;
    --ink-soft: #e6e6e6;
    --brand-green: #7dc242;
    --brand-green-light: #c9e8a8;
    --emboss: #3a3a3a;
    --rule: #4f7a2c;
  }
  * { box-sizing: border-box; margin: 0; padding: 0; }
  html, body { width: 1200px; height: 875px; overflow: hidden; }
  body {
    background: var(--stage);
    font-family: "Montserrat", sans-serif;
    position: relative;
  }
  .card {
    position: absolute;
    left: 270px;
    width: 660px;
    height: 377px;
    background: var(--card);
    border-radius: 22px;
    overflow: hidden;
    box-shadow: 0 10px 28px rgba(0,0,0,0.28);
  }
  .card--front { top: 38px; }
  .card--back { top: 460px; }

  /* Brand wordmark */
  .wordmark {
    position: absolute;
    display: flex;
    align-items: center;
    gap: 12px;
    font-weight: 800;
    text-transform: uppercase;
  }
  .wordmark__square { width: 22px; height: 22px; flex: none; }
  .wordmark__text { line-height: 1.05; }
  .wordmark__sub { display: block; font-size: 0.42em; letter-spacing: 0.32em; }

  .card--front .wordmark {
    left: 50%; top: 50%;
    transform: translate(-50%, -50%);
    font-size: 46px;
    color: var(--emboss);
  }
  .card--front .wordmark__square { background: var(--emboss); width: 30px; height: 30px; }

  .card--back .wordmark {
    left: 50px; top: 178px;
    font-size: 30px;
    color: var(--ink-white);
  }
  .card--back .wordmark__square { background: var(--ink-white); }

  .divider {
    position: absolute;
    left: 318px; top: 100px;
    width: 1px; height: 150px;
    background: var(--rule);
  }

  .contact {
    position: absolute;
    left: 345px; top: 82px;
    color: var(--ink-white);
  }
  .contact__name {
    font-size: 27px;
    font-weight: 800;
    color: var(--brand-green);
    text-transform: uppercase;
    letter-spacing: 0.01em;
  }
  .contact__title {
    font-size: 14px;
    font-weight: 500;
    margin-top: 2px;
    margin-bottom: 18px;
  }
  .contact__list { list-style: none; }
  .contact__item {
    display: flex;
    align-items: center;
    gap: 9px;
    font-size: 14px;
    font-weight: 500;
    margin-bottom: 7px;
    color: var(--ink-soft);
  }
  .contact__icon { width: 13px; height: 13px; flex: none; }

  .swoosh { position: absolute; left: 0; top: 0; width: 660px; height: 377px; }
  .swoosh__url {
    font-family: "Montserrat", sans-serif;
    font-size: 15px;
    font-weight: 600;
    fill: var(--ink-white);
  }
</style>
</head>
<body>

<section class="card card--front" aria-label="Card front">
  <div class="wordmark">
    <span class="wordmark__square"></span>
    <span class="wordmark__text">Tallbrook<span class="wordmark__sub">Design + Build</span></span>
  </div>
</section>

<section class="card card--back" aria-label="Card back">
  <svg class="swoosh" viewBox="0 0 660 377" aria-hidden="true">
    <path d="M310 377 C 450 335, 570 295, 660 245 L660 377 Z" fill="var(--brand-green)"/>
    <path d="M275 377 C 420 322, 560 275, 655 228" fill="none" stroke="var(--brand-green-light)" stroke-width="3"/>
    <path id="url-path" d="M420 372 C 500 352, 580 325, 652 290" fill="none"/>
    <text class="swoosh__url"><textPath href="#url-path" startOffset="6%">www.tallbrookbuild.com</textPath></text>
  </svg>

  <div class="wordmark">
    <span class="wordmark__square"></span>
    <span class="wordmark__text">Tallbrook<span class="wordmark__sub">Design + Build</span></span>
  </div>

  <div class="divider"></div>

  <div class="contact">
    <h1 class="contact__name">Dana Whitfield</h1>
    <p class="contact__title">Owner/CEO</p>
    <ul class="contact__list">
      <li class="contact__item">
        <svg class="contact__icon" viewBox="0 0 24 24" aria-hidden="true"><path fill="var(--brand-green)" d="M6.6 10.8a15.1 15.1 0 0 0 6.6 6.6l2.2-2.2c.3-.3.7-.4 1-.2 1.1.4 2.3.6 3.6.6.6 0 1 .4 1 1V20c0 .6-.4 1-1 1A17 17 0 0 1 3 4c0-.6.4-1 1-1h3.5c.6 0 1 .4 1 1 0 1.300.2 2.500.6 3.600.1.300 0 .700-.2 1z"/></svg>
        07 5550 2100
      </li>
      <li class="contact__item">
        <svg class="contact__icon" viewBox="0 0 24 24" aria-hidden="true"><rect x="6" y="2" width="12" height="20" rx="2" fill="none" stroke="var(--brand-green)" stroke-width="2.4"/><circle cx="12" cy="18" r="1.3" fill="var(--brand-green)"/></svg>
        0400 555 719
      </li>
      <li class="contact__item">
        <svg class="contact__icon" viewBox="0 0 24 24" aria-hidden="true"><rect x="2" y="5" width="20" height="14" rx="1.5" fill="var(--brand-green)"/><path d="M2.5 6 12 13l9.5-7" fill="none" stroke="var(--card)" stroke-width="1.8"/></svg>
        info@tallbrookbuild.com
      </li>
    </ul>
  </div>
</section>

</body>
</html>
```